Website for 3d printing & other services

Hi, i'm after a website to sell my 3d printed automotive parts as well as sell my 3d printing services & other services.

There's a few things i need the website to have:

- Automatic 3d print quoting based on the file the client uploads to the website.
- Shop function where i can sell my custom automotive parts
- 3D printing technologies offered are SLA & FDM
- My business can offer 3d printing, 3d scanning, 3d cad design, cnc machining, steel fabrication, drafting services.

The color design is to suit my logo which is Black, orange & white.

Target Market(s)

3d printing, automotive, fabrication

Industry/Entity Type

General manufacturing & Custom automotive parts

Coding

Coded - Design and coding required

Number of Pages Required

5+ page

Requirements
Must have
• Automatic 3d print quoting. Shop for my printed parts.

```html
<!DOCTYPE html>
<html lang="en">
<head>
<meta charset="utf-8">
<title>KVR Draft &amp; Design</title>
<link href="https://fonts.googleapis.com/css2?family=Exo+2:wght@700;800&family=Roboto:wght@400;500;700&display=swap" rel="stylesheet">
<style>
:root{
  --orange:#f26b0f;
  --orange-deep:#c4500a;
  --black:#000;
  --dark:#0f0f0f;
  --card:#1a1a1a;
  --white:#fff;
  --grey:#cfcfcf;
}
*{margin:0;padding:0;box-sizing:border-box}
html,body{width:1200px;height:4785px;overflow:hidden;background:var(--black)}
body{position:relative;font-family:"Roboto",Arial,sans-serif;color:var(--white)}
.abs{position:absolute}
.heading{font-family:"Exo 2",Arial,sans-serif;font-weight:800;text-transform:uppercase;letter-spacing:1px;text-align:center;color:var(--white)}
.btn{position:absolute;display:flex;align-items:center;justify-content:center;font-size:13px;font-weight:700;text-transform:uppercase;color:var(--white)}
.btn-fill{background:var(--orange)}
.btn-line{border:2px solid var(--orange);background:transparent}
.brand{font-family:"Exo 2",Arial,sans-serif;font-weight:800;color:var(--orange);text-transform:uppercase;line-height:1;text-align:center}
.social{display:flex;gap:7px}
.social span{width:32px;height:32px;border:1.5px solid var(--white);border-radius:50%;display:block}
.photo{position:absolute}

/* header */
.topline{left:0;top:0;width:1200px;height:5px;background:var(--orange)}
.header{left:0;top:5px;width:1200px;height:145px;background:var(--black)}
.header .brand{left:105px;top:30px;width:140px}
.nav{left:332px;top:69px;display:flex;gap:33px;font-size:13px;font-weight:700}
.nav a{color:var(--white);text-decoration:none}
.nav a.active{color:var(--orange)}

/* hero */
.hero{left:0;top:150px;width:1200px;height:705px;background:linear-gradient(120deg,#3a1a0c 0%,#1c2f38 40%,#0f4a5a 70%,#2a1e16 100%)}
.hero-title{left:0;top:360px;width:1200px;font-size:42px}
.hero-sub{left:0;top:420px;width:1200px;text-align:center;font-size:20px;line-height:30px;font-weight:500}

/* about */
.about-mark{left:110px;top:880px;width:440px;height:300px;display:flex;align-items:center;justify-content:center;font-size:150px}
.about-title{left:620px;top:870px;font-size:36px;text-align:left}
.about-text{left:620px;top:938px;width:470px;font-size:14px;line-height:26.6px;color:var(--grey)}

/* products */
.products{left:0;top:1255px;width:1200px;height:703px;background:var(--black)}
.products-title{left:0;top:1355px;width:1200px;font-size:38px;line-height:46px}
.product{position:absolute;top:1490px;width:229px}
.product .photo{position:relative;width:229px;height:240px;background:var(--white);border:1px solid #ddd}
.product .thumb{position:absolute;left:40px;top:60px;width:150px;height:120px;border-radius:20px}
.label{display:block;text-align:center;font-size:16px;font-weight:700;text-decoration:underline;text-underline-offset:4px;text-transform:uppercase}
.product .label{margin-top:22px}

/* tech */
.tech{left:0;top:1958px;width:1200px;height:593px;background:radial-gradient(circle at 50% 40%,#f57a22 0%,var(--orange) 45%,var(--orange-deep) 100%)}
.tech-title{left:0;top:2030px;width:1200px;font-size:36px}
.tech-card{position:absolute;top:2123px;width:476px;height:343px;border:7px solid var(--white);padding:8px;background:var(--orange)}
.tech-card .photo{position:relative;width:100%;height:100%;display:flex;align-items:center;justify-content:center;font-size:22px;font-weight:700}

/* services */
.services{left:0;top:2551px;width:1200px;height:803px;background:var(--dark)}
.services-title{left:0;top:2625px;width:1200px;font-size:36px}
.service{position:absolute;width:305px}
.service .photo{position:relative;width:305px;height:222px;border:3px solid var(--white)}
.service.highlight .photo{border-color:var(--orange)}
.service .label{margin-top:30px}

/* testimonials */
.testi-title{left:0;top:3452px;width:1200px;font-size:36px}
.testi{position:absolute;top:3541px;width:305px;height:277px;background:var(--card);padding:24px 22px}
.stars{color:var(--orange);font-size:14px;letter-spacing:2px}
.testi p{margin-top:10px;font-size:14px;line-height:27px;color:var(--grey)}
.testi hr{border:0;border-top:1px solid #333;margin:16px 0 14px}
.person{display:flex;align-items:center;gap:16px}
.avatar{width:54px;height:54px;border-radius:50%;background:linear-gradient(135deg,#e9e0d6,#c98a5a)}
.person b{display:block;font-size:13px}
.person small{font-size:11px;color:var(--grey)}
.arrow{position:absolute;top:3663px;width:34px;height:34px;border-radius:50%}

/* quote */
.quote{left:0;top:3932px;width:1200px;height:510px;background:linear-gradient(180deg,#1b1b1b,#121212)}
.quote-title{left:0;top:3995px;width:1200px;font-size:36px}
.field{position:absolute;height:44px;background:var(--white);color:#333;font-size:13px;padding:0 16px;display:flex;align-items:center;justify-content:space-between}

/* footer */
.footer-brand{left:500px;top:4470px;width:200px}
.footer-nav{left:0;top:4594px;width:1200px;display:flex;justify-content:center;gap:28px;font-size:15px;font-weight:500}
.footer-contact{left:0;top:4629px;width:1200px;display:flex;justify-content:center;align-items:center;gap:22px;font-size:15px}
.footer-contact span{display:flex;align-items:center;gap:9px}
.footer-social{left:524px;top:4666px}
.divider{left:110px;top:4724px;width:980px;height:1px;background:#333}
.copyright{left:0;top:4748px;width:1200px;text-align:center;font-size:13px}
</style>
</head>
<body>

<div class="abs topline"></div>
<header class="abs header">
  <div class="abs brand"><div style="font-size:46px">KVR</div><div style="font-size:14px;margin-top:8px">Draft &amp; Design</div></div>
  <nav class="abs nav">
    <a class="active" href="#">Home</a><a href="#">About Us</a><a href="#">Products</a><a href="#">Services</a><a href="#">Contact Us</a>
  </nav>
  <div class="btn btn-line" style="left:842px;top:47px;width:130px;height:48px">Get a Quote</div>
  <div class="abs social" style="left:1008px;top:56px" aria-label="Social links"><span></span><span></span><span></span><span></span></div>
</header>

<section class="abs hero" role="img" aria-label="Hand reaching toward a 3D printer printing a white part"></section>
<h1 class="abs heading hero-title">KVR Draft &amp; Design</h1>
<p class="abs hero-sub">Lorem ipsum dolor sit amet, consectetur adipis<br>elit sed do nisi eiusmodea.</p>
<div class="btn btn-fill" style="left:525px;top:500px;width:150px;height:45px">Explore More</div>

<svg class="abs" style="left:0;top:660px" width="1200" height="600" viewBox="0 0 1200 600">
  <polygon points="0,140 600,35 1200,195 1200,600 0,600" fill="#0a0a0a"/>
  <polyline points="0,143 600,14 1200,190" fill="none" stroke="#f26b0f" stroke-width="7"/>
  <polygon points="520,35 600,8 680,35 600,28" fill="#f26b0f"/>
</svg>

<div class="abs about-mark brand" aria-label="KVR">KVR</div>
<h2 class="abs heading about-title">About KVR</h2>
<p class="abs about-text">Lorem ipsum dolor sit amet, consectetur adipiscing elit, sed do eiusmod tempor incididunt ut labore et dolore magna aliqua. Ut enim ad minim veniam, quis nostrud exercitation ullamco laboris nisi ut aliquip ex ea commodo consequat. Duis aute irure dolor in reprehenderit in voluptate velit esse cillum dolore eu fugiat nulla pariatur. Excepteur sint occaecat cupidatat non proident, sunt in culpea.</p>
<div class="btn btn-line" style="left:620px;top:1127px;width:132px;height:45px">Learn More</div>

<section class="abs products"></section>
<h2 class="abs heading products-title">Custom Automotive<br>Parts</h2>
<div class="product" style="left:111px"><div class="photo"><div class="thumb" role="img" aria-label="Grey metal suspension knuckle" style="background:linear-gradient(135deg,#c9c9c9,#8a8a8a)"></div></div><span class="label">Lorem ipsum dol</span></div>
<div class="product" style="left:361px"><div class="photo"><div class="thumb" role="img" aria-label="Blue gear assembly on black housing" style="background:linear-gradient(135deg,#2a6fd1,#1a1a1a)"></div></div><span class="label">Lorem ipsum dol</span></div>
<div class="product" style="left:611px"><div class="photo"><div class="thumb" role="img" aria-label="Colour printer rollers" style="background:linear-gradient(135deg,#e23ca0,#f2e12a 50%,#2ac0e0)"></div></div><span class="label">Lorem ipsum dol</span></div>
<div class="product" style="left:861px"><div class="photo"><div class="thumb" role="img" aria-label="Light grey printed camshaft part" style="background:linear-gradient(135deg,#e0e0e0,#9e9e9e)"></div></div><span class="label">Lorem ipsum dol</span></div>
<div class="btn btn-line" style="left:540px;top:1815px;width:118px;height:45px">Shop All</div>

<section class="abs tech"></section>
<h2 class="abs heading tech-title">3D Printing Technologies</h2>
<div class="tech-card" style="left:111px"><div class="photo" role="img" aria-label="SLA resin printer with parts on build plate" style="background:linear-gradient(160deg,#b9c6dc,#5f78a8)">SLA</div></div>
<div class="tech-card" style="left:615px"><div class="photo" role="img" aria-label="FDM printer heads in operation" style="background:linear-gradient(160deg,#24313f,#10161e 60%,#6a3a20)">FDM</div></div>

<section class="abs services"></section>
<h2 class="abs heading services-title">Our Services</h2>
<div class="service" style="left:111px;top:2715px"><div class="photo" role="img" aria-label="Desktop 3D printer in a workshop" style="background:linear-gradient(135deg,#c7cdd4,#2b2b2b)"></div><span class="label">3D Printing</span></div>
<div class="service" style="left:447px;top:2715px"><div class="photo" role="img" aria-label="Object on a 3D scanning platform" style="background:linear-gradient(135deg,#0c2440,#2d7ab8)"></div><span class="label">3D Scanning</span></div>
<div class="service" style="left:783px;top:2715px"><div class="photo" role="img" aria-label="Engineers working on CAD models at monitors" style="background:linear-gradient(135deg,#1c2a3a,#5e7a96)"></div><span class="label">3D CAD Design</span></div>
<div class="service" style="left:111px;top:3007px"><div class="photo" role="img" aria-label="CNC machine milling a metal block" style="background:linear-gradient(135deg,#e6ebef,#6e7780)"></div><span class="label">CNC Machining</span></div>
<div class="service highlight" style="left:447px;top:3007px"><div class="photo" role="img" aria-label="Welder cutting steel with sparks" style="background:linear-gradient(135deg,#2a2420,#d98a3a 55%,#1a1410)"></div><span class="label">Steel Fabrication</span></div>
<div class="service" style="left:783px;top:3007px"><div class="photo" role="img" aria-label="Drafter working at a computer in an office" style="background:linear-gradient(135deg,#d8dfe6,#4a5866)"></div><span class="label">Drafting Services</span></div>

<h2 class="abs heading testi-title">Testimonials</h2>
<div class="arrow" style="left:35px;background:#2a2a2a"><svg width="34" height="34" viewBox="0 0 34 34"><path d="M19 11l-6 6 6 6" stroke="#fff" stroke-width="2.5" fill="none"/></svg></div>
<div class="arrow" style="left:1131px;background:var(--orange)"><svg width="34" height="34" viewBox="0 0 34 34"><path d="M15 11l6 6-6 6" stroke="#fff" stroke-width="2.5" fill="none"/></svg></div>
<div class="testi" style="left:111px"><div class="stars">★★★★★</div><p>Lorem ipsum dolor sit amet, consect adipiscing elit, sed do eiusmod temp incididunt ut labore et dolore magna t enim ad minim veniam.</p><hr><div class="person"><div class="avatar" role="img" aria-label="Customer portrait"></div><div><b>DANA MORROW</b><small>United States</small></div></div></div>
<div class="testi" style="left:447px"><div class="stars">★★★★★</div><p>Lorem ipsum dolor sit amet, consect adipiscing elit, sed do eiusmod temp incididunt ut labore et dolore magna t enim ad minim veniam.</p><hr><div class="person"><div class="avatar" role="img" aria-label="Customer portrait"></div><div><b>DANA MORROW</b><small>United States</small></div></div></div>
<div class="testi" style="left:783px"><div class="stars">★★★★★</div><p>Lorem ipsum dolor sit amet, consect adipiscing elit, sed do eiusmod temp incididunt ut labore et dolore magna t enim ad minim veniam.</p><hr><div class="person"><div class="avatar" role="img" aria-label="Customer portrait"></div><div><b>DANA MORROW</b><small>United States</small></div></div></div>

<section class="abs quote"></section>
<h2 class="abs heading quote-title">Get a Quote</h2>
<div class="field" style="left:236px;top:4070px;width:358px">Full Name</div>
<div class="field" style="left:605px;top:4070px;width:359px">Phone</div>
<div class="field" style="left:236px;top:4126px;width:358px">Email</div>
<div class="field" style="left:605px;top:4126px;width:359px">Upload File<svg width="14" height="14" viewBox="0 0 14 14"><circle cx="7" cy="4" r="3" fill="#333"/><path d="M1 13c0-4 12-4 12 0z" fill="#333"/></svg></div>
<div class="field" style="left:236px;top:4183px;width:728px">Message</div>

<svg class="abs" style="left:0;top:4245px" width="1200" height="540" viewBox="0 0 1200 540">
  <polygon points="0,10 600,190 1200,10 1200,540 0,540" fill="#000"/>
  <polyline points="0,8 600,188 1200,8" fill="none" stroke="#f26b0f" stroke-width="7"/>
  <polygon points="0,0 240,70 0,30" fill="#f26b0f"/>
  <polygon points="1200,0 960,70 1200,30" fill="#f26b0f"/>
</svg>
<div class="btn btn-fill" style="left:525px;top:4244px;width:149px;height:45px">Send Message</div>

<div class="abs brand footer-brand"><div style="font-size:46px">KVR</div><div style="font-size:14px;margin-top:8px">Draft &amp; Design</div></div>
<nav class="abs footer-nav"><span>HOME</span><span>|</span><span>ABOUT US</span><span>|</span><span>PRODUCTS</span><span>|</span><span>SERVICES</span><span>|</span><span>CONTACT US</span></nav>
<div class="abs footer-contact">
  <span><svg width="14" height="14" viewBox="0 0 24 24"><path d="M6 2l4 4-2 3c1 3 4 6 7 7l3-2 4 4-3 4C10 22 2 14 2 5z" fill="#f26b0f"/></svg>+1 (555) 014 2280</span>
  <span>|</span>
  <span><svg width="16" height="12" viewBox="0 0 16 12"><rect width="16" height="12" fill="#f26b0f"/><path d="M0 0l8 6 8-6" stroke="#000" fill="none"/></svg>info@kvrdraft.com</span>
</div>
<div class="abs social footer-social" aria-label="Social links"><span></span><span></span><span></span><span></span></div>
<div class="abs divider"></div>
<p class="abs copyright">© 2023 KVR DRAFT &amp; DESIGN &nbsp;|&nbsp; All Rights Reserved</p>

</body>
</html>
```